Website for software company "velora"

We need a website for our software company/startup named "velora". We are developing several products (currently 3 standard-software products) which are all in different sectors, but all our products are available for Laptops/PC/Mobile Phones/Tablets, ... We do also create custom software and support our customers with consulting to optimize their processes.
We already have a Logo which you can find in the attached files.
We are a young team of 4 members (two founders and 2 employees).

To get an idea of our products -> the first one is a planning software for healthcare organizations (eg. BlueHaven, firebrigade, pharmacy), the second one is a booking software for sport clubs and the third one is a competition software for sports hunting. You see very diverse. Include or ignore this info of our products as you like.

The design has to be a bootstrap 4 (or higher) design. We have licenced FontAwesome as iconset. Responsive design should come without saying.

• Starting page, product pages, news section, contact, team, services

```html
<!DOCTYPE html>
<html lang="en">
<head>
<meta charset="utf-8">
<title>velora — Software &amp; Process Consulting</title>
<link href="https://fonts.googleapis.com/css2?family=Montserrat:wght@300;400;500;600;700;800&display=swap" rel="stylesheet">
<style>
:root{
  --orange:#f7792b;
  --orange-deep:#ec6418;
  --navy:#232a37;
  --navy-deep:#1a202b;
  --ink:#1f2430;
  --text:#4d5360;
  --muted:#7b808b;
  --light:#f1f2f5;
  --line:#d9dce2;
  --white:#ffffff;
}
*{box-sizing:border-box;margin:0;padding:0}
html,body{width:1200px;height:4370px;overflow:hidden}
body{font-family:"Montserrat",sans-serif;color:var(--text);background:var(--white);position:relative}
.abs{position:absolute}
.btn{position:absolute;display:flex;align-items:center;justify-content:center;border-radius:30px;background:var(--orange);color:var(--white);font-weight:700;letter-spacing:.5px;text-transform:uppercase}
.btn-outline{position:absolute;display:flex;align-items:center;justify-content:center;border-radius:20px;border:2px solid var(--orange);color:var(--orange);font-weight:700;font-size:10px;text-transform:uppercase}

/* header */
.hero{position:absolute;left:0;top:0;width:1200px;height:640px}
.hero-photo{position:absolute;left:0;top:0;width:1200px;height:640px}
.nav{position:absolute;left:0;top:0;width:1200px;height:80px;border-bottom:1px solid rgba(255,255,255,.12)}
.brand{position:absolute;left:132px;top:20px;font-size:42px;font-weight:700;color:var(--white);letter-spacing:1px;line-height:42px}
.nav-link{position:absolute;top:32px;font-size:12px;font-weight:700;color:var(--white);letter-spacing:.5px}
.nav-link.active::after{content:"";position:absolute;left:0;right:0;top:24px;height:2px;background:var(--orange)}
.nav-cta{left:959px;top:22px;width:124px;height:35px;font-size:12px}
.hero-kicker{left:132px;top:218px;font-size:32px;font-weight:400;color:var(--white);letter-spacing:.5px}
.hero-title{left:132px;top:254px;font-size:41px;font-weight:800;color:var(--white);line-height:46px;letter-spacing:.5px}
.hero-copy{left:137px;top:356px;width:420px;font-size:15px;line-height:23px;color:#d4d8df}
.hero-cta{left:132px;top:428px;width:190px;height:50px;font-size:15px}

/* about */
.eyebrow{left:0;width:1200px;top:756px;text-align:center;color:var(--orange);font-size:14px;letter-spacing:.5px}
.section-title{position:absolute;left:0;width:1200px;text-align:center;font-size:34px;font-weight:300;color:var(--ink);letter-spacing:.5px}
.section-title b{font-weight:700}
.about-copy{left:250px;width:700px;top:826px;text-align:center;font-size:14px;line-height:23px}
.feature{position:absolute;top:1008px;width:277px;height:210px;background:var(--white);box-shadow:0 2px 14px rgba(0,0,0,.09);border-radius:4px;padding:38px 36px 0 38px}
.feature h3{margin-top:20px;font-size:18px;font-weight:700;color:var(--ink)}
.feature p{margin-top:10px;font-size:13px;line-height:20px}

/* products */
.products{left:0;top:1324px;width:1200px;height:604px;background:var(--light)}
.underline{position:absolute;left:555px;top:1416px;width:72px;height:3px;background:var(--orange)}
.product-icon{position:absolute;border-radius:10px;display:flex;align-items:center;justify-content:center}
.product-title{position:absolute;font-size:27px;font-weight:700;line-height:34px;letter-spacing:.5px}
.product-copy{position:absolute;font-size:14px;line-height:25px}
.product-btn{height:42px;font-size:13px}
.booking{left:0;top:1928px;width:1200px;height:553px;background:radial-gradient(circle at 30% 40%,#2e3645,#1b212c 70%)}
.circle-art{position:absolute;border-radius:50%}

/* news */
.news{left:0;top:3027px;width:1200px;height:545px;background:var(--light)}
.news-title{left:132px;top:3076px;font-size:34px;font-weight:300;color:var(--ink)}
.news-title b{font-weight:700}
.news-img{position:absolute;top:3148px;width:297px;height:200px}
.news-card{position:absolute;top:3314px;width:274px;height:187px;background:var(--white);padding:24px 22px 0}
.news-card .date{font-size:11px;font-weight:700;color:var(--ink)}
.news-card h4{margin-top:12px;font-size:13.5px;font-weight:700;line-height:19px;color:var(--ink)}
.news-card p{margin-top:6px;font-size:11px;line-height:19px;color:var(--muted)}
.news-card .btn-outline{position:relative;margin-top:10px;width:112px;height:30px}

/* contact */
.contact{left:0;top:3572px;width:1200px;height:460px;background:linear-gradient(180deg,#2c3442 0%,#3b4452 45%,#262d39 100%)}
.field{position:absolute;background:var(--white);border:1px solid #cfd3da;font-size:12px;color:var(--ink);padding:16px 16px}
.contact-btn{left:518px;top:3922px;width:149px;height:41px;font-size:13px}

/* footer */
.footer-brand{left:139px;top:4088px;font-size:40px;font-weight:700;color:var(--ink);letter-spacing:1px}
.footer-copy{left:139px;top:4152px;width:235px;font-size:10.5px;line-height:15px;color:var(--muted)}
.divider{position:absolute;top:4035px;width:1px;height:204px;background:var(--line)}
.foot-head{position:absolute;top:4093px;font-size:13px;font-weight:700;color:var(--ink);letter-spacing:.3px}
.foot-head::before{content:"";position:absolute;left:-17px;top:3px;border-left:6px solid var(--ink);border-top:5px solid transparent;border-bottom:5px solid transparent}
.foot-link{position:absolute;font-size:12px;color:var(--text)}
.social{position:absolute;top:4127px;width:28px;height:28px;border-radius:50%;background:var(--ink)}
.social.first{background:var(--orange)}
.bottom-line{left:0;top:4310px;width:1200px;height:1px;background:var(--line)}
.copyright{left:0;top:4332px;width:1200px;text-align:center;font-size:11px;color:var(--muted)}
</style>
</head>
<body>

<!-- hero -->
<svg class="hero" viewBox="0 0 1200 640" width="1200" height="640" aria-hidden="true">
  <defs>
    <linearGradient id="heroBg" x1="0" y1="0" x2="1" y2="0">
      <stop offset="0" stop-color="#262e3b"/>
      <stop offset=".5" stop-color="#2a3240"/>
      <stop offset="1" stop-color="#3a3130"/>
    </linearGradient>
  </defs>
  <polygon points="0,0 1200,0 1200,552 492,604 0,556" fill="url(#heroBg)"/>
  <polygon points="0,556 492,604 1200,552 1200,566 492,630 0,574" fill="#f7792b"/>
</svg>
<div class="abs" role="img" aria-label="Photo of hands typing on a laptop showing an analytics dashboard" style="left:560px;top:80px;width:640px;height:470px;background:radial-gradient(ellipse at 60% 45%,rgba(200,205,215,.55),rgba(120,90,70,.35) 45%,rgba(40,46,58,0) 75%)"></div>

<header class="nav">
  <div class="brand">velora</div>
  <span class="nav-link active" style="left:420px">PRODUCT</span>
  <span class="nav-link" style="left:544px">SERVICES</span>
  <span class="nav-link" style="left:667px">NEWS</span>
  <span class="nav-link" style="left:767px">TEAM</span>
  <span class="nav-link" style="left:863px">ABOUT</span>
  <span class="btn nav-cta">CONTACT</span>
</header>

<div class="abs hero-kicker">WE HELP CUSTOMER</div>
<h1 class="abs hero-title">TO OPTIMIZE THEIR<br>PROCESSES</h1>
<p class="abs hero-copy">Lorem ipsum dolor sit amet, consectetur adipiscing elit, sed do eiusmod tempor incididunt.</p>
<span class="btn hero-cta">LEARN MORE</span>

<!-- about -->
<div class="abs eyebrow">WHY WE ARE</div>
<h2 class="section-title" style="top:776px">ABOUT <b>VELORA</b></h2>
<p class="abs about-copy">Lorem ipsum dolor sit amet, consectetur adipiscing elit, sed do eiusmod tempor incididunt ut laborLorem ipsum dolor sit amet, consectetur adipiscing elit, sed do eiusmo</p>
<svg class="abs" style="left:0;top:880px" width="1200" height="110" viewBox="0 0 1200 110" fill="none" stroke="#c9cdd4" stroke-width="2" aria-hidden="true">
  <path d="M603 10 V105"/>
  <path d="M594 10 V40 Q594 58 576 58 H340 Q320 58 320 78 V105"/>
  <path d="M612 10 V40 Q612 58 630 58 H866 Q884 58 884 78 V105"/>
</svg>

<div class="feature" style="left:168px">
  <svg width="46" height="46" viewBox="0 0 46 46" fill="none" stroke="#f7792b" stroke-width="2"><circle cx="23" cy="23" r="20"/><circle cx="23" cy="23" r="12" stroke-dasharray="5 3"/><circle cx="23" cy="23" r="6"/></svg>
  <h3>OPTIMIZE</h3>
  <p>Lorem ipsum dolor sit amet, consectetur adipiscing elit, sed do eiusmod tempo</p>
</div>
<div class="feature" style="left:462px;padding-top:34px">
  <svg width="50" height="46" viewBox="0 0 50 46" fill="none" stroke="#f7792b" stroke-width="2"><circle cx="26" cy="14" r="9" stroke-dasharray="4 2"/><circle cx="26" cy="14" r="4"/><path d="M4 34 H16 Q22 34 26 38 H36 Q40 38 46 32"/><path d="M16 34 Q22 30 30 32"/></svg>
  <h3 style="margin-top:18px">SUPPORT</h3>
  <p>Lorem ipsum dolor sit amet, consectetur adipiscing elit, sed do eiusmod tempo</p>
</div>
<div class="feature" style="left:753px">
  <svg width="48" height="46" viewBox="0 0 48 46" fill="none" stroke="#f7792b" stroke-width="2"><rect x="3" y="5" width="42" height="28" rx="2"/><path d="M24 33 V41 M14 41 H34"/><path d="M18 15 L14 19 L18 23 M30 15 L34 19 L30 23 M26 13 L22 25"/></svg>
  <h3>DEVELOP</h3>
  <p>Lorem ipsum dolor sit amet, consectetur adipiscing elit, sed do eiusmod tempo</p>
</div>

<!-- products -->
<section class="abs products"></section>
<h2 class="section-title" style="top:1372px">OUR <b>PRODUCTS</b></h2>
<div class="underline"></div>

<div class="product-icon" style="left:132px;top:1481px;width:78px;height:72px;background:var(--navy)">
  <svg width="44" height="40" viewBox="0 0 44 40" fill="none" stroke="#fff" stroke-width="2"><rect x="6" y="4" width="32" height="22" rx="2"/><path d="M2 30 H42 L38 35 H6 Z"/><circle cx="22" cy="14" r="5"/><path d="M19.5 14 L21.5 16 L25 12"/></svg>
</div>
<h3 class="product-title" style="left:132px;top:1570px;color:var(--ink)">PLANNING SOFTWARE</h3>
<p class="product-copy" style="left:132px;top:1618px;width:410px">Lorem ipsum dolor sit amet, consectetur adipiscing elit, sed do eiusmod tempor incididunt ut labore et dolore magna aliqua. Ut enim ad minim veniam, quis nostrud exercitation ullamco laboris nisi ut aliquip ex ea</p>
<span class="btn product-btn" style="left:132px;top:1750px;width:158px;height:40px">LEARN MORE</span>
<div class="circle-art" role="img" aria-label="Laptop showing the planning software dashboard on an orange circle" style="left:638px;top:1444px;width:428px;height:428px;background:radial-gradient(circle at 50% 45%,#ffa25c,#f7792b 55%,#e2611b)"></div>

<!-- booking -->
<section class="abs booking" role="img" aria-label="Dark background with a faint network pattern"></section>
<div class="circle-art" role="img" aria-label="Tablet with keyboard showing the booking software" style="left:111px;top:1966px;width:440px;height:440px;background:radial-gradient(circle at 50% 45%,#d9dce1,#9ea4ad 55%,#5d636d)"></div>
<div class="product-icon" style="left:652px;top:2040px;width:81px;height:74px;background:var(--orange)">
  <svg width="46" height="42" viewBox="0 0 46 42" fill="none" stroke="#fff" stroke-width="2"><rect x="4" y="6" width="38" height="32" rx="3"/><path d="M4 14 H42 M12 2 V9 M34 2 V9"/><rect x="10" y="19" width="6" height="5"/><rect x="20" y="19" width="6" height="5"/><rect x="30" y="19" width="6" height="5"/><rect x="10" y="28" width="6" height="5"/><rect x="20" y="28" width="6" height="5"/><path d="M30 30 L32 32 L36 28"/></svg>
</div>
<h3 class="product-title" style="left:652px;top:2130px;color:var(--white)">BOOKING SOFTWARE</h3>
<p class="product-copy" style="left:652px;top:2179px;width:420px;color:#d2d6dd">Lorem ipsum dolor sit amet, consectetur adipiscing elit, sed do eiusmod tempor incididunt ut labore et dolore magna aliqua. Ut enim ad minim veniam, quis nostrud exercitation ullamco laboris nisi ut aliquip ex ea</p>
<span class="btn product-btn" style="left:648px;top:2311px;width:163px;height:41px">LEARN MORE</span>

<!-- hunting -->
<div class="product-icon" style="left:149px;top:2608px;width:80px;height:73px;background:var(--navy)">
  <svg width="44" height="44" viewBox="0 0 44 44" fill="none" stroke="#fff" stroke-width="2"><circle cx="22" cy="22" r="17"/><circle cx="22" cy="22" r="9"/><path d="M22 2 V12 M22 32 V42 M2 22 H12 M32 22 H42"/></svg>
</div>
<h3 class="product-title" style="left:147px;top:2690px;color:var(--ink)">HUNTING BOOKIN<br>SOFTWARE</h3>
<p class="product-copy" style="left:147px;top:2768px;width:430px;line-height:20px">Lorem ipsum dolor sit amet, consectetur adipiscing elit, sed do eiusmod tempor incididunt ut labore et dolore magna aliqua. Ut enim ad minim veniam, quis nostrud exercitation</p>
<span class="btn product-btn" style="left:146px;top:2851px;width:166px;height:44px">LEARN MORE</span>
<div class="circle-art" role="img" aria-label="Tablet and phone showing the competition software over a stag in an orange field" style="left:636px;top:2513px;width:476px;height:476px;background:radial-gradient(circle at 50% 35%,#f5c041,#f39a2a 50%,#e0641a)"></div>

<!-- news -->
<section class="abs news"></section>
<h2 class="abs news-title">LATEST <b>NEWS</b></h2>
<div class="news-img" role="img" aria-label="Photo of a developer coding on screens" style="left:131px;background:linear-gradient(135deg,#5a6470,#1e2733)"></div>
<div class="news-img" role="img" aria-label="Photo of a workplace with dashboards on monitors" style="left:450px;background:linear-gradient(135deg,#e6e9ec,#9ba3ab)"></div>
<div class="news-img" role="img" aria-label="Photo of a team working at computers" style="left:767px;background:linear-gradient(135deg,#8a6a50,#2a3340)"></div>
<article class="news-card" style="left:143px">
  <div class="date">JAN 24, 2022</div>
  <h4>Sed ut perspiciatis unde omnis iste natus error sit voluptatem</h4>
  <p>Lorem ipsum dolor sit amet consectetur adipiscing elit, sed do eiusmod tempor</p>
  <span class="btn-outline">LEARN MORE</span>
</article>
<article class="news-card" style="left:462px">
  <div class="date">JAN 24, 2022</div>
  <h4>Sed ut perspiciatis unde omnis iste natus error sit voluptatem</h4>
  <p>Lorem ipsum dolor sit amet consectetur adipiscing elit, sed do eiusmod tempor</p>
  <span class="btn-outline">LEARN MORE</span>
</article>
<article class="news-card" style="left:779px">
  <div class="date">JAN 24, 2022</div>
  <h4>Sed ut perspiciatis unde omnis iste natus error sit voluptatem</h4>
  <p>Lorem ipsum dolor sit amet consectetur adipiscing elit, sed do eiusmod tempor</p>
  <span class="btn-outline">LEARN MORE</span>
</article>

<!-- contact -->
<section class="abs contact" role="img" aria-label="Blurred photo of an office background"></section>
<h2 class="section-title" style="top:3642px;color:var(--white)">CONTACT <b>VELORA</b></h2>
<div class="field" style="left:212px;top:3720px;width:373px;height:51px">Name*</div>
<div class="field" style="left:212px;top:3781px;width:373px;height:51px">Email address*</div>
<div class="field" style="left:212px;top:3842px;width:373px;height:51px">Phone*</div>
<div class="field" style="left:597px;top:3720px;width:374px;height:173px">Message</div>
<span class="btn contact-btn">CONTACT US</span>

<!-- footer -->
<div class="abs footer-brand">velora</div>
<p class="abs footer-copy">Lorem ipsum dolor sit amet, consectetur adipiscing elit, sed do eiusmod tempor incididunt ut labore et dolore</p>
<div class="divider" style="left:434px"></div>
<div class="divider" style="left:674px"></div>
<div class="divider" style="left:896px"></div>

<div class="foot-head" style="left:452px">NAVIGATION</div>
<span class="foot-link" style="left:453px;top:4127px">About Us</span>
<span class="foot-link" style="left:453px;top:4155px">Products</span>
<span class="foot-link" style="left:453px;top:4184px">Services</span>
<span class="foot-link" style="left:453px;top:4213px">Contact Us</span>

<div class="foot-head" style="left:692px">RESOURCES</div>
<span class="foot-link" style="left:693px;top:4127px">News</span>
<span class="foot-link" style="left:693px;top:4155px">Team</span>
<span class="foot-link" style="left:693px;top:4184px">Privacy Policy</span>

<div class="foot-head" style="left:915px">FOLLOW US</div>
<span class="social first" style="left:913px"></span>
<span class="social" style="left:948px"></span>
<span class="social" style="left:982px"></span>
<span class="social" style="left:1016px"></span>

<div class="abs bottom-line"></div>
<div class="abs copyright">© 2022 Velora &nbsp;| All Rights Reserved</div>

</body>
</html>
```